Ridgeline Journeys business card

please see website
www.ridgelinejourneys.comau

info needed on card
Curtis Halvey
Ph
email
Adventure Riding GPS trails

please use my logo and colours off my site

Curtis Halvey
curtis@ridgelinejourneys.com

```html
<!DOCTYPE html>
<html lang="en">
<head>
<meta charset="utf-8">
<title>Ridgeline Journeys business card</title>
<link rel="stylesheet" href="https://fonts.googleapis.com/css2?family=Open+Sans:wght@400;700&display=swap">
<style>
  :root {
    --brand-yellow: #ffd20f;
    --paper-white: #ffffff;
    --paper-grey: #ececec;
    --ink-dark: #1e1e1e;
    --mark-grey: #6b6b6b;
    --backdrop: #e9e6e1;
  }
  * { box-sizing: border-box; margin: 0; padding: 0; }
  html, body {
    width: 1200px; height: 900px; overflow: hidden;
    background: var(--backdrop);
    font-family: "Open Sans", Arial, sans-serif;
  }
  .sheet {
    width: 1200px; height: 900px;
    display: flex; align-items: center; justify-content: center; gap: 40px;
  }
  .card {
    position: relative;
    width: 540px; height: 309px;
    overflow: hidden;
    box-shadow: 0 6px 18px rgba(0,0,0,.18);
  }
  /* Front */
  .card--front {
    background: var(--brand-yellow);
    color: var(--paper-white);
  }
  .brand {
    display: flex; align-items: center; gap: 18px;
  }
  .brand__square {
    width: 46px; height: 46px; flex: none;
  }
  .brand__name {
    font-weight: 700; font-size: 34px; line-height: 1.02;
    text-transform: uppercase; letter-spacing: .5px;
  }
  .card--front .brand {
    position: absolute; left: 100px; top: 98px;
  }
  .card--front .brand__square { background: var(--paper-white); }
  .tagline {
    position: absolute; left: 0; right: 0; top: 212px;
    text-align: center; font-weight: 700; font-size: 17px;
  }
  /* Back */
  .card--back {
    background: linear-gradient(180deg, var(--paper-white) 0%, var(--paper-grey) 100%);
  }
  .card--back .brand {
    position: absolute; left: 110px; top: 56px; color: var(--ink-dark);
  }
  .card--back .brand__square { background: var(--mark-grey); }
  .contact {
    position: absolute; right: 26px; top: 124px;
    list-style: none; text-align: right;
    color: var(--brand-yellow); font-size: 13px; line-height: 22px;
  }
  .contact li { display: flex; align-items: center; justify-content: flex-end; gap: 8px; }
  .contact svg { width: 14px; height: 14px; flex: none; }
  .name-band {
    position: absolute; left: 0; right: 0; bottom: 0; height: 112px;
    background: var(--brand-yellow);
  }
  .name-band__name {
    position: absolute; left: 34px; top: 34px;
    color: var(--paper-white); font-weight: 700; font-size: 20px;
  }
</style>
</head>
<body>
<main class="sheet">
  <section class="card card--front" aria-label="Card front">
    <div class="brand">
      <span class="brand__square"></span>
      <span class="brand__name">Ridgeline<br>Journeys</span>
    </div>
    <p class="tagline">Adventure Riding GPS trails</p>
  </section>

  <section class="card card--back" aria-label="Card back">
    <div class="brand">
      <span class="brand__square"></span>
      <span class="brand__name">Ridgeline<br>Journeys</span>
    </div>
    <ul class="contact">
      <li>(044)-555-0142
        <svg viewBox="0 0 14 14" aria-hidden="true"><rect width="14" height="14" rx="3" fill="#ffd20f"/><path d="M4 3.5h2l.8 2-1.2.8a5 5 0 0 0 2.1 2.1l.8-1.2 2 .8v2a1 1 0 0 1-1 1A7 7 0 0 1 3 4.5a1 1 0 0 1 1-1z" fill="#fff"/></svg>
      </li>
      <li>info@ridgelinejourneys.com
        <svg viewBox="0 0 14 14" aria-hidden="true"><rect width="14" height="14" rx="3" fill="#ffd20f"/><rect x="3" y="4" width="8" height="6" fill="#fff"/><path d="M3 4l4 3 4-3" stroke="#ffd20f" fill="none"/></svg>
      </li>
      <li>www.ridgelinejourneys.com
        <svg viewBox="0 0 14 14" aria-hidden="true"><rect width="14" height="14" rx="3" fill="#ffd20f"/><circle cx="7" cy="7" r="3.6" fill="none" stroke="#fff" stroke-width="1.2"/><path d="M3.4 7h7.2M7 3.4v7.2" stroke="#fff" stroke-width="1"/></svg>
      </li>
    </ul>
    <div class="name-band">
      <p class="name-band__name">Curtis Halvey</p>
    </div>
  </section>
</main>
</body>
</html>
```